Simple Logo Design for Semi-Clear Plastic Frosted Card stock

Create a business card on frosted plastic. compliment existing logo elements with a tree trunk, roots, or seed at the lower half and the full logo both on the front.

Contact information will go on a solid portion of the back of this design since this card stock is semi-transparent.

It is important to consider this plastic card stock medium in your design. I found helpful tips and guides listed at vellaprint-sample.net: be careful to understand ink printed on plastic cards cannot have too much of a consistent print area or risks peeling and fine lines can easily scratch off.
Updates

2" x 3.5" 20PT Clear Plastic Business cards with Round corners Please get info or templates here: https://www.vellaprint-sample.net/product-detail/2-x-35-20pt-clear-plastic-business-cards-with-round-corners

Target Market(s)

Not for profit- religion

Industry/Entity Type

Business

Must include complementary elements to the existing logo

Font styles to use
Decorative

Colors
000000

Requirements
Must have
• Elements of community, nature and oneness. Such as: seed, roots, tree trunk, etc.
• Three lines of space on the back for Name, Title, Phone Number.
Nice to have
• I like a light use of decorative elements
Should not have
• No eyes, from faces or animals.

```html
<!DOCTYPE html>
<html lang="en">
<head>
<meta charset="utf-8">
<title>Steadfast Grove – Business Card</title>
<link rel="stylesheet" href="https://fonts.googleapis.com/css2?family=Lato:wght@400;700&display=swap">
<style>
  :root {
    --page-bg: #e4e2de;
    --frost-light: #f6f6f4;
    --frost-mid: #e9eae8;
    --band-teal: #1e4844;
    --leaf-green: #2d6b27;
    --ink-teal: #1f4b47;
    --ink-green: #3a7a2c;
    --ink-grey: #4a4d4f;
  }
  html, body {
    margin: 0;
    width: 1200px;
    height: 969px;
    overflow: hidden;
    background: var(--page-bg);
    font-family: "Lato", sans-serif;
  }
  .canvas {
    position: relative;
    width: 1200px;
    height: 969px;
  }
  .card {
    position: absolute;
    left: 100px;
    top: 199px;
    width: 1000px;
    height: 571px;
    border-radius: 30px;
    overflow: hidden;
    background: linear-gradient(135deg, var(--frost-light), var(--frost-mid));
    box-shadow: 0 10px 30px rgba(0,0,0,0.12), inset 0 0 0 1px rgba(255,255,255,0.7);
  }
  .card-art {
    position: absolute;
    inset: 0;
  }
  .brand {
    position: absolute;
    left: 82px;
    top: 218px;
    display: flex;
    align-items: center;
    gap: 16px;
  }
  .brand-dot {
    width: 34px;
    height: 34px;
    border-radius: 50%;
    background: var(--leaf-green);
  }
  .brand-name {
    font-size: 50px;
    font-weight: 400;
    color: var(--ink-teal);
    letter-spacing: 1px;
  }
  .contact {
    position: absolute;
    left: 85px;
    top: 348px;
  }
  .contact-name {
    margin: 0;
    font-size: 36px;
    font-weight: 700;
    color: var(--ink-teal);
    letter-spacing: 0.5px;
  }
  .contact-title {
    margin: 6px 0 0;
    font-size: 30px;
    font-weight: 400;
    color: var(--ink-green);
    letter-spacing: 0.5px;
  }
  .contact-phone {
    margin: 22px 0 0;
    font-size: 30px;
    font-weight: 400;
    color: var(--ink-grey);
    letter-spacing: 1px;
  }
</style>
</head>
<body>
<main class="canvas">
  <section class="card">
    <svg class="card-art" viewBox="0 0 1000 571" width="1000" height="571" aria-hidden="true">
      <path class="teal-band" d="M791,0 C905,40 945,200 890,340 C840,460 715,540 560,571 L1000,571 L1000,0 Z" fill="var(--band-teal)"/>
      <path class="band-edge" d="M791,0 C905,40 945,200 890,340 C840,460 715,540 560,571" fill="none" stroke="#ffffff" stroke-opacity="0.8" stroke-width="4"/>
      <path class="green-swoosh" d="M918,218 C930,380 800,515 545,571 L770,571 C890,495 940,380 918,218 Z" fill="var(--leaf-green)"/>
    </svg>

    <div class="brand">
      <span class="brand-dot"></span>
      <span class="brand-name">STEADFAST GROVE</span>
    </div>

    <div class="contact">
      <p class="contact-name">MARA LINDQVIST</p>
      <p class="contact-title">PRESIDENT</p>
      <p class="contact-phone">555 0142 7789</p>
    </div>
  </section>
</main>
</body>
</html>
```